Calder Vossik - Cinematographer

NEED:
I'm looking for a sleek, professional, modern business card that will give give the recipient the impression that they can trust their production will go smoothly by hiring me. I will bring creativity and knowledge to their shoot, so that we can create powerful images.
I am looking for a card with a strong style and design ethos that could be expanded to a website and a full visual/graphic/design entity for me.
ABOUT ME:
I am a mid-twenties cinematographer, I work on music video, narrative short, commercial, and corporate projects. I blend the science and artistry of cameras and filmmaking to tell a story. I'm an artist, a technician, and a manager.
DESIGN:
I like sleek, simple design. Black, dark grays, white, dark navy, steel blues, I love cyan, but also cyan and red. I am not a fan of earthy tones. I generally prefer modern, san-serif fonts over serifs. My old logo was based on an aperture, a multi-blade device at the back of a lens that controls how much light passes through, but I made it with so many colors, that it doesn't necessarily lend itself to a specific color-scheme or design ethos. I liked that the aperture design provided a sense of the technical requirements of my job. I'm a fan of matte business cards, but am open to plenty of specialty print processes to make an outstanding card.
ATTACHED FILES:
My Old Rainbox Aperture Logo, plus a few designs I've tried playing around with, but am not tied to. I AM OPEN TO NEW DESIGNS, DO NOT FEEL TIED TO THIS.
**I've pulled my old logo down from the attached files, and instead attached other business cards I like, so as not to mislead you where I would like to go.
INFO:
Name: Calder Vossik
Job: Cinematographer
Email: ccvossik@lumenpost.net
Phone: 415.555.0193
Website: caldervossik.com
Updates
I'm adding some images of other cards that I like, and removing my old logo, since I'm looking for something new, and don't want that old logo to push anyone a certain direction.

```html
<!DOCTYPE html>
<html lang="en">
<head>
<meta charset="utf-8">
<title>Calder Vossik – Cinematographer business card</title>
<link rel="stylesheet" href="https://fonts.googleapis.com/css2?family=Montserrat:wght@300;600&family=Roboto:wght@400;700&display=swap">
<style>
  :root {
    --backdrop: #d9d9dc;
    --card-black: #121214;
    --card-black-2: #1f1f22;
    --steel: #8c8d90;
    --steel-light: #b9babd;
    --cyan: #1aa3e8;
    --accent-blue: #1b7fd6;
    --red: #e0554f;
    --white: #f4f4f4;
    --muted: #c9c9cc;
  }
  * { margin: 0; padding: 0; box-sizing: border-box; }
  html, body { width: 1200px; height: 913px; overflow: hidden; }
  body {
    background: var(--backdrop);
    position: relative;
    font-family: "Roboto", Arial, sans-serif;
  }
  .card {
    position: absolute;
    width: 520px;
    height: 297px;
    border-radius: 4px;
    overflow: hidden;
    background: linear-gradient(135deg, var(--card-black-2), var(--card-black) 60%);
    box-shadow: 0 14px 30px rgba(0,0,0,.35);
  }
  .card--front { left: 70px; top: 160px; }
  .card--back { left: 610px; top: 456px; }

  /* Front */
  .brand {
    position: absolute;
    display: flex;
    align-items: center;
    gap: 18px;
  }
  .card--front .brand { left: 78px; top: 104px; }
  .brand__dot {
    border-radius: 50%;
    background: var(--cyan);
    flex: none;
  }
  .card--front .brand__dot { width: 78px; height: 78px; }
  .brand__name {
    font-family: "Montserrat", Arial, sans-serif;
    font-weight: 600;
    color: var(--white);
    text-transform: uppercase;
    letter-spacing: 1px;
    line-height: 1;
  }
  .card--front .brand__name { font-size: 34px; }
  .brand__role {
    font-family: "Montserrat", Arial, sans-serif;
    font-weight: 300;
    color: var(--muted);
    text-transform: uppercase;
    letter-spacing: 5px;
    margin-top: 8px;
  }
  .card--front .brand__role { font-size: 15px; }

  /* Back */
  .back-art { position: absolute; inset: 0; }
  .card--back .brand { left: 30px; top: 34px; gap: 10px; }
  .card--back .brand__dot { width: 38px; height: 38px; }
  .card--back .brand__name { font-size: 17px; }
  .card--back .brand__role { font-size: 8px; letter-spacing: 3px; margin-top: 4px; }
  .divider {
    position: absolute;
    left: 30px; top: 96px;
    width: 220px; height: 1px;
    background: var(--white);
  }
  .identity { position: absolute; left: 30px; top: 108px; }
  .identity__name { color: var(--accent-blue); font-weight: 700; font-size: 19px; }
  .identity__role { color: var(--white); font-size: 13px; margin-top: 3px; }
  .contact {
    position: absolute;
    left: 30px; top: 172px;
    list-style: none;
    color: var(--white);
    font-size: 13px;
  }
  .contact li { display: flex; align-items: center; gap: 12px; margin-bottom: 9px; }
  .contact svg { width: 15px; height: 15px; fill: var(--accent-blue); flex: none; }
</style>
</head>
<body>

<section class="card card--front" aria-label="Card front">
  <div class="brand">
    <span class="brand__dot"></span>
    <div>
      <div class="brand__name">Calder Vossik</div>
      <div class="brand__role">Cinematographer</div>
    </div>
  </div>
</section>

<section class="card card--back" aria-label="Card back">
  <svg class="back-art" viewBox="0 0 520 297" preserveAspectRatio="none" aria-hidden="true">
    <defs>
      <linearGradient id="steelPanel" x1="0" y1="0" x2="1" y2="1">
        <stop offset="0" stop-color="var(--steel)"/>
        <stop offset="1" stop-color="var(--steel-light)"/>
      </linearGradient>
    </defs>
    <polygon points="240,0 520,0 520,210" fill="url(#steelPanel)"/>
    <line x1="240" y1="0" x2="520" y2="210" stroke="var(--red)" stroke-width="2"/>
    <line x1="478" y1="0" x2="458" y2="297" stroke="var(--cyan)" stroke-width="4"/>
  </svg>

  <div class="brand">
    <span class="brand__dot"></span>
    <div>
      <div class="brand__name">Calder Vossik</div>
      <div class="brand__role">Cinematographer</div>
    </div>
  </div>
  <div class="divider"></div>
  <div class="identity">
    <div class="identity__name">Calder Vossik</div>
    <div class="identity__role">Cinematographer</div>
  </div>
  <ul class="contact">
    <li>
      <svg viewBox="0 0 24 24" aria-hidden="true"><path d="M6.6 10.8a15.1 15.1 0 0 0 6.6 6.6l2.2-2.2a1 1 0 0 1 1-.25 11.4 11.4 0 0 0 3.6.57 1 1 0 0 1 1 1V20a1 1 0 0 1-1 1A17 17 0 0 1 3 4a1 1 0 0 1 1-1h3.5a1 1 0 0 1 1 1c0 1.25.2 2.45.57 3.57a1 1 0 0 1-.25 1z"/></svg>
      <span>415.555.0193</span>
    </li>
    <li>
      <svg viewBox="0 0 24 24" aria-hidden="true"><path d="M2 5h20v14H2z M2 5l10 8 10-8" fill="var(--accent-blue)"/><path d="M2 5l10 8 10-8" fill="none" stroke="var(--card-black)" stroke-width="1.6"/></svg>
      <span>ccvossik@lumenpost.net</span>
    </li>
    <li>
      <svg viewBox="0 0 24 24" aria-hidden="true"><circle cx="12" cy="12" r="10"/><path d="M2 12h20M12 2c3 3 3 17 0 20M12 2c-3 3-3 17 0 20" fill="none" stroke="var(--card-black)" stroke-width="1.4"/></svg>
      <span>www.caldervossik.com</span>
    </li>
  </ul>
</section>

</body>
</html>
```